Business Name: DM Space Arranging Pty Ltd

Business Type: Professional Home Styling and Minor Renovation Business

Logo: Attached is the logo that has been created.
I always envisaged the logo in the middle of the business card with my full name underneath it.

Marnie Tulloch B.Com LMR HTV
Property Stylist & Project Manager

Include dot points of services
Staging Houses for Sale
Minor Home Renovations
Home Styling & Project Management
Re-Designing Living Spaces to Aid the Disabled

Somewhere on the card I would like to incorporate
"Property Styling and Cosmetic Renovations"

Colour Scheme:
Gloss black business card, with white and then
Gold or Silver as the highlight colours.

Incorporate a small amount of yellow only if possible to make it pop. If this really doesn’t work it doesn’t have to be used. Also l like the colour teal if that needs to be used as a contrast colour.

Feel/Themes
• I love antique chairs, regal expensive looking furniture mixed with modern homes (this is the unique style I want to sell) antique and modern mix that looks high class as well as modern and fresh, targeting an executive market.
• I want to use an orchid as a trademark throughout the course of my work, not sure if this can somehow be incorporated? Also really like crowns to give that regal/antique feel and then something else to give that modern twist (I don’t know what the something else could be)
• Wall Paper Look (on a portion of it not all of it, like a French look)
• Overall feel - A very deluxe and professional feel with a little bit of creative flare.

I hope this helps create a bit of a picture.

Is it ok that I call you tomorrow morning? My mobile number is 0438 926 574 if you have any questions for me in the meantime.

Target Market(s)

High Quality Executive Market - People selling homes

Industry/Entity Type

Business

Contact Information for Business Card

Include dot points of services:
Staging Houses for Sale
Minor Home Renovations

Font styles to use
Serif
Script

Colors
33b8a4
fbed22

Requirements
Must have
• Marnie Tulloch B.Com LMR HTV
• Property Stylist & Project Manager
• LMR and HTV Logos on the card
• "Dramatically increase the value of your property"
Nice to have
• Colour Scheme:
• Gloss black business card, with white and then
• Gold or Silver as the highlight colours.
• Incorporate a small amount of yellow only if possible to make it pop. If this really doesn’t work it doesn’t have to be used. Also l like the colour teal if that needs to be used as a contrast colour.
• Also like teal as a highlight colour.

```html
<!DOCTYPE html>
<html lang="en">
<head>
<meta charset="utf-8">
<title>DM Space Arranging Pty Ltd — Business Cards</title>
<link rel="stylesheet" href="https://fonts.googleapis.com/css2?family=Great+Vibes&family=Tinos:wght@400&display=swap">
<style>
  :root {
    --bg: #3b3b3d;
    --card: #ffffff;
    --ink: #1a1a1a;
    --black: #111111;
    --gold: #c9a24a;
    --gold-light: #ecd38a;
    --gold-dark: #8a6a22;
    --rule: #6b6b6b;
    --ornament: #ececec;
  }
  * { box-sizing: border-box; margin: 0; padding: 0; }
  html, body { width: 1200px; height: 852px; overflow: hidden; }
  body {
    background: radial-gradient(ellipse at 45% 40%, #525254 0%, var(--bg) 60%, #262628 100%);
    font-family: "Tinos", "Times New Roman", serif;
    color: var(--ink);
    position: relative;
  }
  .card {
    position: absolute;
    width: 540px;
    height: 310px;
    background: var(--card);
    border-radius: 12px;
    overflow: hidden;
    box-shadow: 0 12px 28px rgba(0,0,0,.45);
  }
  .card--services { left: 60px; top: 90px; }
  .card--contact { left: 600px; top: 450px; }
  .card__art { position: absolute; inset: 0; }

  .ornament {
    position: absolute;
    background: radial-gradient(ellipse, var(--ornament) 0%, rgba(255,255,255,0) 70%);
  }
  .brand {
    position: absolute;
    display: flex;
    align-items: center;
    gap: 8px;
  }
  .brand__mark {
    width: 14px; height: 14px;
    border-radius: 50%;
    background: var(--gold);
    flex: none;
  }
  .brand__name {
    font-size: 13px;
    letter-spacing: 2.5px;
    text-transform: uppercase;
    color: var(--gold-dark);
    border-top: 1px solid var(--rule);
    border-bottom: 1px solid var(--rule);
    padding: 3px 6px;
    white-space: nowrap;
  }

  /* services card */
  .card--services .ornament { left: 30px; top: 100px; width: 200px; height: 110px; }
  .card--services .brand { left: 36px; top: 148px; }
  .badges { position: absolute; right: 24px; top: 26px; display: flex; gap: 8px; }
  .badge { height: 62px; background: var(--black); }
  .badge--htv { width: 110px; border: 2px solid var(--gold); }
  .badge--lmr { width: 170px; border: 2px solid var(--black); background: linear-gradient(90deg, var(--black) 60%, #ffffff 60%); }
  .services {
    position: absolute;
    left: 46px; top: 188px;
    list-style: none;
    font-size: 15.5px;
    line-height: 1.45;
  }
  .services li::before { content: "» "; }

  /* contact card */
  .card--contact .ornament { left: 250px; top: 10px; width: 230px; height: 100px; }
  .card--contact .brand { right: 26px; top: 58px; }
  .person { position: absolute; left: 34px; top: 92px; }
  .person__name { font-family: "Great Vibes", cursive; font-size: 36px; line-height: 1; font-weight: 400; }
  .person__role { font-size: 14.5px; line-height: 1.2; margin-top: 6px; }
  .contact { position: absolute; left: 36px; top: 208px; list-style: none; font-size: 15px; line-height: 1.4; }
  .contact li { display: flex; align-items: center; gap: 10px; }
  .contact svg { width: 13px; height: 13px; fill: var(--ink); flex: none; }
  .tagline {
    position: absolute;
    left: 392px; top: 178px;
    width: 140px;
    color: #ffffff;
    font-size: 15px;
    line-height: 1.3;
  }
</style>
</head>
<body>

<section class="card card--services" aria-label="Services side">
  <svg class="card__art" viewBox="0 0 540 310" aria-hidden="true">
    <defs>
      <linearGradient id="goldBand" x1="0" y1="1" x2="1" y2="0">
        <stop offset="0" stop-color="#8a6a22"/>
        <stop offset=".45" stop-color="#f3dc95"/>
        <stop offset="1" stop-color="#b88b2e"/>
      </linearGradient>
    </defs>
    <path d="M200 310 L540 222 L540 232 L250 310 Z" fill="url(#goldBand)"/>
    <path d="M150 310 L215 292 L255 310 Z" fill="#111111"/>
  </svg>
  <div class="ornament" role="img" aria-label="Faint decorative flourish behind the company name"></div>
  <div class="badges">
    <div class="badge badge--htv" role="img" aria-label="HTV membership badge"></div>
    <div class="badge badge--lmr" role="img" aria-label="LMR membership badge"></div>
  </div>
  <div class="brand">
    <span class="brand__mark"></span>
    <span class="brand__name">DM Space Arranging Pty Ltd</span>
  </div>
  <ul class="services">
    <li>Staging Homes for Sale » Minor Home Renovations</li>
    <li>Home Styling, Project &amp; Budget Management » Source</li>
    <li>Furnishings &amp; Accessories » Re-Designing Rooms for the Disabled</li>
  </ul>
</section>

<section class="card card--contact" aria-label="Contact side">
  <svg class="card__art" viewBox="0 0 540 310" aria-hidden="true">
    <defs>
      <linearGradient id="goldSwoosh" x1="0" y1="1" x2="1" y2="0">
        <stop offset="0" stop-color="#8a6a22"/>
        <stop offset=".5" stop-color="#f1d98e"/>
        <stop offset="1" stop-color="#a8802c"/>
      </linearGradient>
    </defs>
    <path d="M330 310 C385 262 370 175 430 128 C470 98 515 82 540 72 L540 310 Z" fill="#111111"/>
    <path d="M0 296 C190 298 320 262 365 178 C395 122 455 92 540 66" fill="none" stroke="url(#goldSwoosh)" stroke-width="5"/>
    <path d="M20 304 C210 304 330 272 378 190 C410 135 460 104 540 80" fill="none" stroke="url(#goldSwoosh)" stroke-width="2"/>
    <path d="M0 310 L0 302 C200 306 300 296 330 310 Z" fill="url(#goldSwoosh)"/>
  </svg>
  <div class="ornament" role="img" aria-label="Faint decorative flourish behind the company name"></div>
  <div class="brand">
    <span class="brand__mark"></span>
    <span class="brand__name">DM Space Arranging Pty Ltd</span>
  </div>
  <div class="person">
    <h1 class="person__name">Marnie Tulloch</h1>
    <p class="person__role">B.Com LMR HTV<br>Property Stylist &amp;<br>Project Manager</p>
  </div>
  <ul class="contact">
    <li><svg viewBox="0 0 16 16"><path d="M3 1l3 3-1.5 2a9 9 0 0 0 5.5 5.5L12 10l3 3-2 2C7 15 1 9 1 3z"/></svg>00 00 000 00 0</li>
    <li><svg viewBox="0 0 16 16"><path d="M1 3h14v10H1z M1 3l7 6 7-6" fill="none" stroke="#1a1a1a" stroke-width="1.6"/></svg>yourname@yourwebsite.com</li>
    <li><svg viewBox="0 0 16 16"><circle cx="8" cy="8" r="7"/><path d="M1 8h14M8 1c-3 4-3 10 0 14M8 1c3 4 3 10 0 14" stroke="#fff" stroke-width="1" fill="none"/></svg>www.yourwebsite.com</li>
  </ul>
  <p class="tagline">Dramatically Increase the Value of Your Home</p>
</section>

</body>
</html>
```